Electronics Recycling and IT Asset Disposition Flyer and Brochure Design

We need a 2 side A5 Flyer and 4 side A4 folder( brochure) for our electronics waste recycling and IT asset management and disposition business.
Our business provides free electronics waste recycling for companies, schools, learning institutions,councils, IT companies and government sectors. Many people are ignorant of responsible recycling of electronics which could harm our health if not treated properly.
The list of other services attached in the pdf.
We provide an end to end and tailored solution for our customers from collection, logistics, data sanitisation, remarketing and recycling.

The Flyer should create awareness of responsible electronics recycling and drive the audience to contact us or go to our website to learn more about the company and services.A brief list of services should also be included in the flyer.The goal is to get the audience to contact us to enquire more about our services.

The Brochure should include all the above plus provide more details about the company, processes, services,contact details (fb, linkedin,Twitter). The goal is to convert the audience to customers for recycling and provide other services as added services.

The final design for both flyer and brochure should communicate responsible recycling of electronic scrap and tailored solution for every organisation.

The company website is www.kelvane-scrap.com.au based in Australia. We serve clients nationwide.

Target Market(s)

IT companies, Corporate, schools and learning institutions, government sector

Industry/Entity Type

Recycling

Contact Information for Business Card

Name: Harold Pendrake
email: harold@kelvane-scrap.com.au
website: www.kelvane-scrap.com.au
mobile: +614 612 39057
Phone: 1300 46 2735

Font styles to use
Serif

Requirements
Must have
• I would like the designs to have more images and icons
Nice to have
Should not have
• none

```html
<!DOCTYPE html>
<html lang="en">
<head>
<meta charset="utf-8">
<title>Kelvane Scrap – Service Offering Flyer</title>
<link rel="stylesheet" href="https://fonts.googleapis.com/css2?family=Fira+Sans+Condensed:wght@500;600&family=Fira+Sans:ital,wght@1,300;1,400&display=swap">
<style>
  :root {
    --green: #4cb82a;
    --green-bright: #5fd21f;
    --green-deep: #1f8f3d;
    --dot: #13924a;
    --charcoal: #232323;
    --charcoal-soft: #3a3a3a;
    --paper: #f6f6f6;
    --ink: #1b1b1b;
    --backdrop: #e4e4e4;
  }
  * { box-sizing: border-box; margin: 0; padding: 0; }
  html, body { width: 1200px; height: 1200px; overflow: hidden; }
  body { background: var(--backdrop); position: relative; font-family: "Fira Sans", sans-serif; color: var(--ink); }

  .flyer {
    position: absolute; left: 200px; top: 33px; width: 800px; height: 1134px;
    background: linear-gradient(180deg, #ffffff 0%, var(--paper) 100%);
    overflow: hidden;
  }
  .header { position: absolute; left: 0; top: 0; width: 800px; height: 390px; }
  .brand {
    position: absolute; left: 58px; top: 110px; width: 240px; display: flex; align-items: flex-start; gap: 14px;
    font-family: "Fira Sans Condensed", sans-serif; font-weight: 600; font-size: 62px; line-height: 1.02;
    color: var(--green);
  }
  .brand-dot { width: 26px; height: 26px; border-radius: 50%; background: var(--green); flex: none; margin-top: 22px; }

  .section-title {
    font-family: "Fira Sans Condensed", sans-serif; font-weight: 600; font-size: 23px; line-height: 28px;
    color: var(--green); margin-bottom: 10px;
  }
  .bullets { list-style: none; font-style: italic; font-weight: 300; font-size: 17px; line-height: 24px; }
  .bullets li { position: relative; padding-left: 26px; }
  .bullets li::before {
    content: ""; position: absolute; left: 1px; top: 7px; width: 11px; height: 11px; border-radius: 50%; background: var(--dot);
  }
  .bullets li.plain::before { display: none; }
  .bullets .pass { padding-left: 0; display: block; }
  .bullets .pass::before { content: "*"; color: var(--green); font-style: normal; margin-right: 2px; }

  .service { position: absolute; }
  .col-divider { position: absolute; width: 1px; background: linear-gradient(180deg, transparent, #d6d6d6 30%, #d6d6d6 70%, transparent); }

  .feature-box {
    position: absolute; left: 32px; top: 678px; width: 737px; height: 332px;
    border: 3px solid var(--green); border-radius: 48px 0 60px 0;
    background: linear-gradient(180deg, #ffffff 0%, #f4f4f4 100%);
    box-shadow: 0 14px 18px -12px rgba(0,0,0,0.35);
  }
  .bullets.boxed li::before { background: var(--green); }

  .footer { position: absolute; left: 0; top: 1063px; width: 800px; height: 71px; }
  .footer-line {
    position: absolute; left: 0; top: 10px; width: 712px; height: 61px; display: flex; align-items: center; justify-content: center;
    white-space: nowrap;
    font-family: "Fira Sans Condensed", sans-serif; font-weight: 600; font-size: 19px; color: var(--ink);
  }
</style>
</head>
<body>
<main class="flyer">
  <svg class="header" viewBox="0 0 800 390">
    <defs>
      <linearGradient id="photoTone" x1="0" y1="0" x2="1" y2="1">
        <stop offset="0" stop-color="#f4f5f6"/>
        <stop offset="0.45" stop-color="#b9c6cf"/>
        <stop offset="0.7" stop-color="#7f9a5e"/>
        <stop offset="1" stop-color="#d9dcdc"/>
      </linearGradient>
      <linearGradient id="darkTone" x1="0" y1="0" x2="1" y2="1">
        <stop offset="0" stop-color="#3b3b3b"/>
        <stop offset="1" stop-color="#1e1e1e"/>
      </linearGradient>
      <linearGradient id="bandTone" x1="0" y1="0" x2="1" y2="0">
        <stop offset="0" stop-color="#3fae1f"/>
        <stop offset="1" stop-color="#5fd21f"/>
      </linearGradient>
    </defs>
    <rect width="800" height="390" fill="#ffffff"/>
    <polygon points="318,0 800,0 800,254 392,310" fill="url(#photoTone)" role="img" aria-label="Photo of a light bulb holding a tree on a green meadow, wind turbines behind"/>
    <polygon points="0,0 318,0 390,312 800,270 800,300 0,372" fill="url(#darkTone)"/>
    <polygon points="0,356 800,252 800,282 0,372" fill="url(#bandTone)"/>
    <polygon points="0,372 800,282 800,300 0,390" fill="#ffffff"/>
    <polygon points="420,334 800,286 800,300 420,346" fill="var(--charcoal)"/>
    <polygon points="382,312 396,310 334,38 324,40" fill="var(--green)"/>
    <polygon points="300,46 322,6 352,36" fill="var(--green)"/>
  </svg>
  <div class="brand"><span class="brand-dot"></span><span>Kelvane<br>Scrap</span></div>

  <section class="service" style="left:42px; top:413px; width:335px;">
    <h2 class="section-title">Secure E-Waste Collection Service</h2>
    <ul class="bullets">
      <li>Kelvane Scrap collects electronic waste from schools, businesses, home users and government departments</li>
      <li>Secure collection includes pick up of e-waste and transportation to our recycling facility in a secured truck</li>
      <li>Registration of assets and reporting</li>
    </ul>
  </section>
  <div class="col-divider" style="left:387px; top:400px; height:250px;"></div>
  <section class="service" style="left:409px; top:413px; width:370px;">
    <h2 class="section-title">Certified Data Erasure Services</h2>
    <ul class="bullets">
      <li>To provide secure data destruction:
        <span class="pass">X1 pass</span>
        <span class="pass">X3 pass (Recommended, DoD standard)</span>
        <span class="pass">X7 pass</span>
      </li>
      <li>Total destruction of HDDs by degaussing</li>
      <li>Total physical destruction of any storage media by shredding</li>
    </ul>
  </section>

  <div class="feature-box"></div>
  <section class="service" style="left:52px; top:722px; width:330px;">
    <h2 class="section-title" style="margin-bottom:18px;">Receipting Registration,<br>Test &amp; Audit Services</h2>
    <ul class="bullets boxed">
      <li>Registering your assets on our Asset Management System</li>
      <li>Test, audit and verify specifications, condition and resale value</li>
      <li class="plain">Provide a detailed asset report</li>
      <li>Cleaning and removal of company logos and asset tags</li>
    </ul>
  </section>
  <div class="col-divider" style="left:387px; top:705px; height:290px;"></div>
  <section class="service" style="left:418px; top:722px; width:335px;">
    <h2 class="section-title" style="margin-bottom:6px;">IT Asset Remarketing</h2>
    <ul class="bullets boxed">
      <li>Recover client’s IT asset and mobile devices for valuation and remarketing</li>
    </ul>
    <h2 class="section-title" style="margin-top:8px; margin-bottom:6px;">Processing &amp; recycling of<br>electronic waste</h2>
    <ul class="bullets boxed">
      <li>All assets with no market value will be processed as E-Waste and recycled with zero to landfill in our ISO certified partner refinery overseas for metal recovery</li>
    </ul>
  </section>

  <footer class="footer">
    <svg width="800" height="71" viewBox="0 0 800 71" style="position:absolute;left:0;top:0;">
      <rect width="800" height="71" fill="var(--charcoal)"/>
      <polygon points="0,10 683,10 712,71 0,71" fill="url(#bandTone)"/>
    </svg>
    <p class="footer-line">Kelvane Scrap | 18-22 Foundry Street, Marsden Park 2765 NSW | Service Offering</p>
  </footer>
</main>
</body>
</html>
```